KAJU Freightways #ALLKAJU Business Cards & Letterhead

I am looking to business cards designed for our organization. We are currently undergoing a small re-branding that is taking place. Our organization is called KAJU Freightways and we are headquartered in Phoenix, AZ. We primarily provide transportation and logistics services to the Marlow Parcel Bureau who is our largest customer. I would like to see a design that incorporates name, title, contact info, website, and address (this will be different depending on the employee). I would also like to see some color on the business card using our logo colors or a variation. I would like our logo on the back of the business card with the website displayed. The final design should communicate that we are a next generation transportation operate that focuses on being driver-first, customer-centric, innovative, and sustainable.We would also like our #ALLKAJU catch phrase incorporated as well.

Target Market(s)

Transportation & Logistics

Industry/Entity Type

Trucking Company

Contact Information for Business Card

-First and Last Name
-Position Title
-Contact Phone
-Contact Email
-Physical Address

Font styles to use
Serif

Colors

Designer to choose colors to be used in the design.

Requirements
Must have
• -KAJU logo prominently displayed
• -#ALLKAJU catch phrase used
• -Some amount of color, design gradient, etc.
• -Logo on the back with website listed (https://www.kajufreightco.example)

```html
<!DOCTYPE html>
<html lang="en">
<head>
<meta charset="utf-8">
<title>KAJU Freightways Business Card</title>
<link href="https://fonts.googleapis.com/css2?family=Roboto+Slab:wght@400;500;700&display=swap" rel="stylesheet">
<style>
  :root {
    --page: #3b3b3d;
    --card: #222224;
    --ink: #ffffff;
    --muted: #8b8b8e;
    --green: #7cc522;
    --teal: #0c4352;
  }
  * { box-sizing: border-box; margin: 0; padding: 0; }
  html, body { width: 799px; height: 1200px; overflow: hidden; }
  body {
    background: var(--page);
    font-family: "Roboto Slab", Georgia, serif;
    color: var(--ink);
    position: relative;
  }
  .card {
    position: absolute;
    left: 80px;
    width: 640px;
    height: 366px;
    background: var(--card);
    border-radius: 3px;
    overflow: hidden;
  }
  .card-front { top: 140px; }
  .card-back { top: 690px; }

  /* Front */
  .front-mark {
    position: absolute;
    left: 0; right: 0; top: 118px;
    display: flex; align-items: center; justify-content: center; gap: 16px;
  }
  .front-mark .dot {
    width: 34px; height: 34px; border-radius: 50%;
    border: 2px solid var(--muted);
  }
  .front-mark .name {
    font-size: 62px; font-weight: 700; color: var(--muted); letter-spacing: 2px; line-height: 1;
  }
  .front-url {
    position: absolute; left: 0; right: 0; top: 268px;
    display: flex; align-items: center; justify-content: center; gap: 20px;
    font-size: 14px; letter-spacing: 3px; color: #e6e6e6;
  }
  .front-url .dash { width: 36px; height: 3px; background: var(--green); }
  .hashtag {
    position: absolute; left: 0; right: 0; top: 304px;
    text-align: center; font-size: 14px; font-weight: 700;
    letter-spacing: 3px; color: var(--green);
  }

  /* Back */
  .brand {
    position: absolute; left: 28px; top: 26px;
    display: flex; align-items: center; gap: 12px;
  }
  .brand .ring {
    width: 26px; height: 26px; border-radius: 50%; border: 3px solid var(--green);
  }
  .brand .name { font-size: 44px; font-weight: 700; color: var(--ink); line-height: 1; }
  .tagline {
    position: absolute; left: 240px; top: 34px;
    font-size: 24px; font-weight: 700; line-height: 1.15;
  }
  .person { position: absolute; left: 34px; top: 108px; }
  .person .full-name { font-size: 23px; font-weight: 700; line-height: 1.2; }
  .person .title {
    font-size: 14px; padding-bottom: 6px; margin-top: 2px;
    border-bottom: 1px solid var(--green); display: inline-block; padding-right: 40px;
  }
  .address {
    position: absolute; left: 34px; top: 186px;
    font-size: 14px; line-height: 1.4; font-style: normal;
  }
  .contacts {
    position: absolute; left: 350px; top: 206px;
    list-style: none; font-size: 14px;
  }
  .contacts li { display: flex; align-items: center; gap: 12px; height: 24px; white-space: nowrap; }
  .contacts svg { width: 14px; height: 14px; fill: var(--green); flex: none; }
  .stripe {
    position: absolute; left: 0; bottom: 56px; width: 300px; height: 9px;
    background: var(--green);
  }
  .band {
    position: absolute; left: 290px; right: 0; bottom: 0; height: 56px;
    background: var(--teal);
    border-top-left-radius: 22px;
    display: flex; align-items: center; padding-left: 40px;
    font-size: 17px; white-space: nowrap;
  }
</style>
</head>
<body>
  <section class="card card-front" aria-label="Card front">
    <div class="front-mark">
      <span class="dot"></span>
      <span class="name">KAJU</span>
    </div>
    <div class="front-url">
      <span class="dash"></span>
      <span>www.kajufreightco.example</span>
      <span class="dash"></span>
    </div>
    <div class="hashtag">#ALLKAJU</div>
  </section>

  <section class="card card-back" aria-label="Card back">
    <div class="brand">
      <span class="ring"></span>
      <span class="name">KAJU</span>
    </div>
    <div class="tagline">Transportation &amp;<br>Energy Services</div>

    <div class="person">
      <div class="full-name">Daniel Hargrove</div>
      <div class="title">Chairman &amp; CEO</div>
    </div>
    <address class="address">4120 North Cedar Ridge<br>Parkway Glendale, AZ 85301</address>

    <ul class="contacts">
      <li>
        <svg viewBox="0 0 24 24"><path d="M6.6 10.8a15.1 15.1 0 0 0 6.6 6.6l2.2-2.2c.3-.3.7-.4 1-.2 1.1.4 2.3.6 3.6.6.6 0 1 .4 1 1V20c0 .6-.4 1-1 1A17 17 0 0 1 3 4c0-.6.4-1 1-1h3.5c.6 0 1 .4 1 1 0 1.3.2 2.5.6 3.6.1.3 0 .7-.2 1z"/></svg>
        <span>555-014-2290</span>
      </li>
      <li>
        <svg viewBox="0 0 24 24"><path d="M2 5h20v14H2zm2 2v.5l8 5 8-5V7l-8 5z"/></svg>
        <span>daniel@kajufreightco.example</span>
      </li>
      <li>
        <svg viewBox="0 0 24 24"><path d="M12 2a10 10 0 1 0 0 20 10 10 0 0 0 0-20zm6.9 6h-3a15 15 0 0 0-1.3-3.9A8 8 0 0 1 18.9 8zM12 4c.8 1.2 1.5 2.5 1.9 4h-3.8c.4-1.5 1.1-2.8 1.9-4zM4.3 14a8 8 0 0 1 0-4h3.4a16 16 0 0 0 0 4zm.8 2h3a15 15 0 0 0 1.3 3.9A8 8 0 0 1 5.1 16zm3-8h-3a8 8 0 0 1 4.3-3.9C8.8 5.3 8.4 6.6 8.1 8zM12 20c-.8-1.2-1.5-2.5-1.9-4h3.8c-.4 1.5-1.1 2.8-1.9 4zm2.3-6H9.7a14 14 0 0 1 0-4h4.6a14 14 0 0 1 0 4zm.3 5.9c.6-1.2 1-2.5 1.3-3.9h3a8 8 0 0 1-4.3 3.9zm1.7-5.9a16 16 0 0 0 0-4h3.4a8 8 0 0 1 0 4z"/></svg>
        <span>www.kajufreightco.example</span>
      </li>
    </ul>

    <div class="stripe"></div>
    <div class="band">KAJU Freightways &amp; Energy</div>
  </section>
</body>
</html>
```